Ancient Art and Artifact information website

Hello Designers,
We are starting up a new website who talk abut and discusses an ancient arts artifacts. We would covering a wide range of countries ranging from Egypt, Greece, India, Syria, Rome, etc. My website name Bright Loom
Designs that fits with ancient theme and some kind of uniqueness would be accepted.
Requirements:
1) A home page design
2) Sub page design
3) A suitable logo
Sections can be added are featured ancient arts/places with short description followed by a more button, latest news, and comment section.
Add contents if you found relevant for this category of website. Ability to share the information through social media is desired.
Must be a responsive design. I look forward to designs which are mind blowing.
Number of Pages Required
2 page

```html
<!DOCTYPE html>
<html lang="en">
<head>
<meta charset="utf-8">
<title>Bright Loom — Ancient Arts &amp; Artifacts</title>
<link href="https://fonts.googleapis.com/css2?family=Open+Sans:ital,wght@0,400;0,600;0,700;1,400&family=Raleway:wght@500&family=Roboto:wght@400;500;700&family=Roboto+Condensed:wght@700&display=swap" rel="stylesheet">
<style>
:root{
  --orange:#d9820b;
  --ink:#333333;
  --text:#666666;
  --muted:#999999;
  --line:#e5e5e5;
  --soft:#f2f2f2;
  --footer:#333333;
  --white:#ffffff;
  --name:#3b5b9a;
}
*{margin:0;padding:0;box-sizing:border-box}
html,body{width:1200px;height:2817px;overflow:hidden}
body{position:relative;background:var(--white);font-family:"Open Sans",Arial,sans-serif;color:var(--text)}
.abs{position:absolute}
.media{position:absolute;display:block}

/* header */
.site-header{position:absolute;left:0;top:0;width:1200px;height:88px;background:var(--white);box-shadow:0 1px 4px rgba(0,0,0,.08);z-index:2}
.brand{position:absolute;left:100px;top:22px;font-family:"Roboto Condensed",sans-serif;font-weight:700;font-size:36px;color:var(--ink);letter-spacing:-.5px}
.main-nav{position:absolute;top:37px;font-family:"Roboto",sans-serif;font-size:14px;color:var(--ink)}
.search-icon{position:absolute;left:1077px;top:38px}

/* hero */
.hero{position:absolute;left:0;top:88px;width:1200px;height:485px;background:linear-gradient(180deg,#3f79b8 0%,#7fa9cf 30%,#c9a66f 55%,#b07c42 80%,#8e5f30 100%)}
.hero-caption{position:absolute;left:100px;top:233px;width:351px;height:195px;background:rgba(20,20,20,.72);padding:28px 18px}
.hero-caption h1{font-family:"Roboto",sans-serif;font-weight:700;font-size:40px;color:var(--white);letter-spacing:.5px;line-height:1}
.hero-caption p{font-size:13.5px;color:var(--white);line-height:22px;margin-top:12px;font-weight:600}
.btn-outline{display:inline-block;border:1px solid #ccc;border-radius:2px;font-size:11px;font-weight:600;padding:6px 12px;color:var(--white);margin-top:18px}
.slider-arrow{position:absolute;width:34px;height:34px;border-radius:50%;background:rgba(30,30,30,.8);top:315px}

/* welcome */
.welcome{position:absolute;left:0;top:573px;width:1200px;height:413px;background:var(--soft)}
.welcome-frame{position:absolute;left:100px;top:62px;width:394px;height:282px;background:var(--white);border:1px solid #ddd;padding:6px}
.welcome-frame .media{left:6px;top:6px;right:6px;bottom:6px;background:linear-gradient(180deg,#6b8fc4 0%,#c7b4a6 35%,#a4713f 60%,#7b5a3b 100%)}
.welcome-body{position:absolute;left:524px;top:66px;width:576px}
.section-title{font-family:"Roboto",sans-serif;font-weight:400;font-size:25px;color:var(--ink);text-transform:uppercase}
.welcome-body p{font-size:11.4px;line-height:20.5px;color:var(--text);margin-top:16px}
.welcome-body p + p{margin-top:14px}
.btn-dark-outline{display:inline-block;border:1px solid #555;border-radius:2px;font-size:11px;color:var(--ink);padding:7px 10px;margin-top:18px}

/* featured */
.featured-title{left:98px;top:1040px}
.news-title{left:834px;top:1033px}
.art-item{position:absolute;left:100px;width:670px;height:227px}
.art-item .media{left:0;top:0;width:306px;height:227px}
.art-info{position:absolute;left:334px;top:0;width:336px}
.art-info h3{font-family:"Raleway",sans-serif;font-weight:500;font-size:18px;line-height:24px;color:var(--orange)}
.meta{display:flex;margin-top:14px;font-size:12.5px;font-style:italic;color:var(--text);align-items:center}
.meta span{display:flex;align-items:center;gap:8px}
.meta .sep{width:1px;height:14px;background:var(--line);margin:0 18px}
.art-info p{font-size:11.4px;line-height:20.5px;margin-top:12px}
.btn-orange{display:inline-block;background:var(--orange);color:var(--white);font-size:11px;font-weight:700;padding:7px 10px;margin-top:14px}
.divider{position:absolute;left:100px;width:670px;height:1px;background:var(--line)}

/* news */
.news-card{position:absolute;left:836px;width:264px;height:251px;border:1px solid #ddd;background:var(--white);box-shadow:0 1px 3px rgba(0,0,0,.06)}
.news-card .media{left:0;top:0;width:262px;height:131px}
.date-badge{position:absolute;left:0;top:107px;background:var(--orange);color:var(--white);font-size:11.5px;padding:4px 14px;font-weight:600}
.news-card p{position:absolute;left:16px;top:145px;width:236px;font-size:11px;line-height:20px;color:var(--ink)}
.news-tag{position:absolute;left:16px;top:215px;font-size:11px;color:var(--ink);display:flex;gap:8px;align-items:center}

/* comments */
.comment-box{position:absolute;left:100px;top:1972px;width:668px;height:481px;border:1px solid #ddd;background:var(--white)}
.avatar{position:absolute;width:42px;height:42px;border-radius:50%;background:linear-gradient(135deg,#b98c6a,#6e4d36)}
.person-name{position:absolute;font-size:15px;color:var(--name);font-weight:600}
.person-sub{position:absolute;font-size:11px;color:var(--muted)}
.rule{position:absolute;height:1px;background:var(--line)}
.post-title{position:absolute;left:198px;top:168px;font-family:"Roboto",sans-serif;font-size:17px;color:var(--text)}
.post-text{position:absolute;left:198px;top:200px;width:430px;font-size:11px;line-height:20px;color:var(--text)}
.actions{position:absolute;left:22px;top:322px;display:flex;gap:22px;font-size:10px;color:var(--text);align-items:center}
.actions span{display:flex;align-items:center;gap:6px}
.comment-input{position:absolute;left:73px;top:362px;width:571px;height:60px;border:1px solid #ddd;border-radius:3px;padding:12px 10px;font-size:11px;color:var(--muted)}
.post-btn{position:absolute;left:543px;top:440px;width:101px;height:26px;border:1px solid #ddd;background:#f7f7f7;font-size:11px;color:var(--text);text-align:center;line-height:24px}

/* places */
.places{position:absolute;left:836px;top:1968px;width:278px;height:229px;border:1px solid #ddd;background:var(--white)}
.places h4{background:var(--orange);color:var(--white);font-family:"Roboto",sans-serif;font-weight:500;font-size:20px;height:52px;line-height:52px;padding-left:16px}
.places ul{list-style:none;padding:8px 0 0}
.places li{height:34px;line-height:34px;font-size:12px;color:var(--ink);padding-left:18px;border-bottom:1px solid #eee;display:flex;align-items:center;gap:10px}
.places li:last-child{border-bottom:none}

.follow{position:absolute;left:836px;top:2239px;width:278px;height:218px;border:1px solid #ddd;background:var(--white)}
.follow h4{position:absolute;top:-12px;left:70px;width:138px;text-align:center;background:var(--white);font-family:"Roboto",sans-serif;font-weight:400;font-size:19px;color:var(--ink)}
.tile{position:absolute;width:75px;height:77px;color:var(--white);text-align:center;font-size:11px;line-height:14px;padding-top:12px}
.tile b{display:block;font-size:13px;font-weight:700;line-height:18px;margin-bottom:6px}

/* footer */
.site-footer{position:absolute;left:0;top:2548px;width:1200px;height:269px;background:var(--footer)}
.footer-brand{position:absolute;left:0;width:1200px;top:2606px;text-align:center;font-family:"Roboto Condensed",sans-serif;font-weight:700;font-size:38px;color:var(--white)}
.footer-links{position:absolute;left:0;width:1200px;top:2677px;text-align:center;font-size:12.5px;color:var(--white)}
.copyright{position:absolute;left:0;width:1200px;top:2707px;text-align:center;font-size:12px;color:var(--white)}
.footer-social{position:absolute;left:0;width:1200px;top:2738px;display:flex;justify-content:center;gap:14px;font-size:11px;font-weight:600;color:var(--white)}
</style>
</head>
<body>

<header class="site-header">
  <div class="brand">Bright Loom</div>
  <nav>
    <span class="main-nav" style="left:600px">HOME</span>
    <span class="main-nav" style="left:675px">ABOUT</span>
    <span class="main-nav" style="left:758px">ANCIENT ARTS</span>
    <span class="main-nav" style="left:886px">PLACES</span>
    <span class="main-nav" style="left:976px">CONTACT US</span>
    <svg class="search-icon" width="16" height="16" viewBox="0 0 16 16"><circle cx="6.5" cy="6.5" r="4.5" fill="none" stroke="#333" stroke-width="2"/><line x1="10" y1="10" x2="14" y2="14" stroke="#333" stroke-width="2.4" stroke-linecap="round"/></svg>
  </nav>
</header>

<section class="hero" role="img" aria-label="Great Sphinx and pyramid under a blue sky in the desert"></section>
<div class="hero-caption">
  <h1>BRIGHT LOOM</h1>
  <p>Sed ut perspiciatis unde omnis iste natus error sit voluptatem accusantium doloremque</p>
  <span class="btn-outline">READ MORE ●</span>
</div>
<svg class="slider-arrow" style="left:34px" viewBox="0 0 34 34"><polyline points="19,11 13,17 19,23" fill="none" stroke="#fff" stroke-width="2.5"/></svg>
<svg class="slider-arrow" style="left:1129px" viewBox="0 0 34 34"><polyline points="15,11 21,17 15,23" fill="none" stroke="#fff" stroke-width="2.5"/></svg>

<section class="welcome">
  <div class="welcome-frame"><div class="media" role="img" aria-label="Ruins of a Minoan palace with red columns"></div></div>
  <div class="welcome-body">
    <h2 class="section-title">Welcome to Bright Loom</h2>
    <p>Sed ut perspiciatis unde omnis iste natus error sit voluptatem accusantium doloremque laudantium, totam rem aperiam, eaque ipsa quae ab illo inventore veritatis et quasi architecto beatae vitae dicta sunt explicabo. Nemo enim ipsam voluptatem quia voluptas sit aspernatur aut odit aut fugit, sed quia consequuntur magni dolores eos qui ratione voluptatem sequi nesciunt. Neque porro quisquam est, qui dolorem ipsum quia dolor sit amet, consectetur, adipisci velit, sed quia</p>
    <p>Nemo enim ipsam voluptatem quia voluptas sit aspernatur aut odit aut fugit, sed quia consequuntur magni dolores eos qui ratione voluptatem sequi nesciunt. Neque porro quisquam est, qui dolorem ipsum quia dolor sit amet, consectetur, adipisci velit, sed quia</p>
    <span class="btn-dark-outline">READ MORE ⊕</span>
  </div>
</section>

<h2 class="section-title abs featured-title">Featured Ancient Arts</h2>
<h2 class="section-title abs news-title">Latest News</h2>

<article class="art-item" style="top:1108px">
  <div class="media" role="img" aria-label="White houses and blue domes above the sea on a Greek island" style="background:linear-gradient(180deg,#5d8fd6 0%,#9cc0ea 35%,#2b5da8 60%,#e7e4de 80%,#c9c2b8 100%)"></div>
  <div class="art-info">
    <h3>Nemo enim ipsam voluptatem<br>quia voluptas sit aspernatur</h3>
    <div class="meta"><span><svg width="11" height="11" viewBox="0 0 11 11"><rect x="0.5" y="1.5" width="10" height="9" fill="none" stroke="#777"/><line x1="0.5" y1="4" x2="10.5" y2="4" stroke="#777"/></svg>Jan 25, 2017</span><i class="sep"></i><span><svg width="12" height="11" viewBox="0 0 12 11"><path d="M1 1h10v7H5l-3 2V8H1z" fill="none" stroke="#777"/></svg>2 comments</span></div>
    <p>Sed ut perspiciatis unde omnis iste natus error sit voluptatem accusantium doloremque laudantium, totam rem aperiam, eaque ipsa quae ab illo inventore veritatis et quasi architecto beatae vitae dicta sunt explicabo. Nemo enim ipsam</p>
    <span class="btn-orange">READ MORE &gt;&gt;</span>
  </div>
</article>
<div class="divider" style="top:1371px"></div>

<article class="art-item" style="top:1399px">
  <div class="media" role="img" aria-label="Ancient domed stone gateway at sunset" style="background:linear-gradient(180deg,#6f8fb8 0%,#e6a979 35%,#a5643a 60%,#6d4a2f 100%)"></div>
  <div class="art-info">
    <h3>Nemo enim ipsam voluptatem<br>quia voluptas sit aspernatur</h3>
    <div class="meta"><span><svg width="11" height="11" viewBox="0 0 11 11"><rect x="0.5" y="1.5" width="10" height="9" fill="none" stroke="#777"/><line x1="0.5" y1="4" x2="10.5" y2="4" stroke="#777"/></svg>Jan 25, 2017</span><i class="sep"></i><span><svg width="12" height="11" viewBox="0 0 12 11"><path d="M1 1h10v7H5l-3 2V8H1z" fill="none" stroke="#777"/></svg>2 comments</span></div>
    <p>Sed ut perspiciatis unde omnis iste natus error sit voluptatem accusantium doloremque laudantium, totam rem aperiam, eaque ipsa quae ab illo inventore veritatis et quasi architecto beatae vitae dicta sunt explicabo. Nemo enim ipsam</p>
    <span class="btn-orange">READ MORE &gt;&gt;</span>
  </div>
</article>
<div class="divider" style="top:1655px"></div>

<article class="art-item" style="top:1683px">
  <div class="media" role="img" aria-label="Carved stone temple interior with pillars" style="background:linear-gradient(135deg,#4a3424 0%,#8a6a4c 45%,#5e4431 70%,#3b2a1d 100%)"></div>
  <div class="art-info">
    <h3>Nemo enim ipsam voluptatem<br>quia voluptas sit aspernatur</h3>
    <div class="meta"><span><svg width="11" height="11" viewBox="0 0 11 11"><rect x="0.5" y="1.5" width="10" height="9" fill="none" stroke="#777"/><line x1="0.5" y1="4" x2="10.5" y2="4" stroke="#777"/></svg>Jan 25, 2017</span><i class="sep"></i><span><svg width="12" height="11" viewBox="0 0 12 11"><path d="M1 1h10v7H5l-3 2V8H1z" fill="none" stroke="#777"/></svg>2 comments</span></div>
    <p>Sed ut perspiciatis unde omnis iste natus error sit voluptatem accusantium doloremque laudantium, totam rem aperiam, eaque ipsa quae ab illo inventore veritatis et quasi architecto beatae vitae dicta sunt explicabo. Nemo enim ipsam</p>
    <span class="btn-orange">READ MORE &gt;&gt;</span>
  </div>
</article>

<article class="news-card" style="top:1100px">
  <div class="media" role="img" aria-label="Market alley with hanging red textiles" style="background:linear-gradient(135deg,#a8324a 0%,#7a4a3a 45%,#c7a27c 75%,#5a3b2c 100%)"></div>
  <span class="date-badge">06 MARCH</span>
  <p>Sed ut perspiciatis unde omnis iste natus error sit voluptatem accusantium remque laudantium, totam rem aperiam</p>
  <span class="news-tag"><svg width="9" height="10" viewBox="0 0 9 10"><circle cx="4.5" cy="3" r="2.5" fill="#333"/><path d="M0 10a4.5 4 0 0 1 9 0z" fill="#333"/></svg>Ancient arts artifacts</span>
</article>
<article class="news-card" style="top:1373px">
  <div class="media" role="img" aria-label="Hanging brass lanterns in a bazaar" style="background:linear-gradient(135deg,#2e2218 0%,#8c6a3f 40%,#c6a46b 60%,#3b2c1f 100%)"></div>
  <span class="date-badge">06 MARCH</span>
  <p>Sed ut perspiciatis unde omnis iste natus error sit voluptatem accusantium remque laudantium, totam rem aperiam</p>
  <span class="news-tag"><svg width="9" height="10" viewBox="0 0 9 10"><circle cx="4.5" cy="3" r="2.5" fill="#333"/><path d="M0 10a4.5 4 0 0 1 9 0z" fill="#333"/></svg>Ancient arts artifacts</span>
</article>
<article class="news-card" style="top:1647px">
  <div class="media" role="img" aria-label="Lantern-lit stone arcade in an old city" style="background:linear-gradient(180deg,#3a2a1e 0%,#9b7550 45%,#6a4b33 75%,#2c1f16 100%)"></div>
  <span class="date-badge">06 MARCH</span>
  <p>Sed ut perspiciatis unde omnis iste natus error sit voluptatem accusantium remque laudantium, totam rem aperiam</p>
  <span class="news-tag"><svg width="9" height="10" viewBox="0 0 9 10"><circle cx="4.5" cy="3" r="2.5" fill="#333"/><path d="M0 10a4.5 4 0 0 1 9 0z" fill="#333"/></svg>Ancient arts artifacts</span>
</article>

<section class="comment-box">
  <div class="avatar" style="left:24px;top:22px" role="img" aria-label="User avatar"></div>
  <span class="person-name" style="left:78px;top:22px">Mara Lenning</span>
  <span class="person-sub" style="left:78px;top:46px">sed do eiusmod tempor incididunt</span>
  <div class="rule" style="left:24px;right:24px;top:78px"></div>
  <div class="avatar" style="left:24px;top:90px" role="img" aria-label="User avatar"></div>
  <span class="person-name" style="left:78px;top:90px">Mara Lenning</span>
  <span class="person-sub" style="left:78px;top:114px">319 Reviews , 432 Followers</span>
  <div class="media" role="img" aria-label="Ruined Greek temple columns" style="left:22px;top:169px;width:150px;height:94px;background:linear-gradient(180deg,#6e98cf 0%,#a9c3df 40%,#b7966a 70%,#6f5a40 100%)"></div>
  <span class="post-title">Sed ut perspiciatis unde omnis iste natus</span>
  <p class="post-text">sed do eiusmod tempor incididunt ut labore et dolore magna aliqua. Ut enim ad minim veniam, quis nostrud exercitation ullamco laboris nisi ut aliquip ex ea commodo consequat. Duis aute irure</p>
  <div class="rule" style="left:24px;right:24px;top:298px"></div>
  <div class="actions">
    <span><svg width="10" height="10" viewBox="0 0 10 10"><path d="M1 4h2v6H1zM4 4l2-4 1 1-1 3h3l-1 6H4z" fill="#888"/></svg>LIKE</span>
    <span><svg width="10" height="9" viewBox="0 0 10 9"><path d="M0 0h10v6H4L1 9V6H0z" fill="#888"/></svg>COMMENT</span>
    <span><svg width="10" height="9" viewBox="0 0 10 9"><path d="M6 0l4 4-4 4V5.5C3 5.5 1 6.5 0 9 0 5 2 3 6 2.5z" fill="#888"/></svg>SHARE</span>
  </div>
  <div class="avatar" style="left:24px;top:358px" role="img" aria-label="User avatar"></div>
  <div class="comment-input">write a comment</div>
  <div class="post-btn">Post Comment</div>
</section>

<aside class="places">
  <h4>PLACES</h4>
  <ul>
    <li><svg width="7" height="10" viewBox="0 0 7 10"><polyline points="1,1 5,5 1,9" fill="none" stroke="#d9820b" stroke-width="2"/></svg>Sed ut perspiciatis unde omnis</li>
    <li><svg width="7" height="10" viewBox="0 0 7 10"><polyline points="1,1 5,5 1,9" fill="none" stroke="#d9820b" stroke-width="2"/></svg>Excepteur sint occaecat</li>
    <li><svg width="7" height="10" viewBox="0 0 7 10"><polyline points="1,1 5,5 1,9" fill="none" stroke="#d9820b" stroke-width="2"/></svg>Ut enim ad minima veniam</li>
    <li><svg width="7" height="10" viewBox="0 0 7 10"><polyline points="1,1 5,5 1,9" fill="none" stroke="#d9820b" stroke-width="2"/></svg>Neque porro quisquam</li>
    <li><svg width="7" height="10" viewBox="0 0 7 10"><polyline points="1,1 5,5 1,9" fill="none" stroke="#d9820b" stroke-width="2"/></svg>Quis autem vel eum iure</li>
  </ul>
</aside>

<aside class="follow">
  <h4>FOLLOW US</h4>
  <div class="tile" style="left:14px;top:32px;background:#3b5998"><b>Folio</b>68,876<br>Fans</div>
  <div class="tile" style="left:98px;top:32px;background:#1da1f2"><b>Chirp</b>65<br>Followers</div>
  <div class="tile" style="left:185px;top:32px;background:#dd4b39"><b>Gleam</b>8,961<br>Followers</div>
  <div class="tile" style="left:14px;top:115px;background:#0e83c0"><b>Linkra</b>68,876<br>Fans</div>
  <div class="tile" style="left:98px;top:115px;background:#d62b2b"><b>Vidra</b>65<br>Followers</div>
  <div class="tile" style="left:185px;top:115px;background:#4a77d4"><b>Pinna</b>8,961<br>Followers</div>
</aside>

<footer class="site-footer"></footer>
<div class="footer-brand">Bright Loom</div>
<div class="footer-links">Home &nbsp;/ featured ancient &nbsp;/ &nbsp;Contact &nbsp;/ &nbsp;Privacy Policy &nbsp;/ &nbsp;Terms &amp; Condition</div>
<div class="copyright">Copyright @ 2017 Bright Loom. All Rights Reserved.</div>
<div class="footer-social"><span>Folio</span><span>Pinna</span><span>Chirp</span><span>Gleam</span><span>Linkra</span></div>

</body>
</html>
```